A Vegan Nutritional Supplement (one Product) website

I am looking for an experienced Web designer to build a One Product website for a Nutritional Supplement that is 100% vegan. The emphasis would be on both the Quality and Quantity of the ingredients and their benefits. It contains Essential Vitamins, Minerals, and a proprietary blend of 42 Fruits and Vegetables. I welcome color suggestions as long as it includes Green (vegan) and White.. The final design should communicate to the buyer: Quality, Healthy, Safety (Natural vegan ingredients), Natural energy, well being. The product includes benefits for 3 vital elements of optimal health: Immune Health, Heart Health, and Brain Health

Industry/Entity Type

Health and Wellness - Nutritional Supplements

Number of Pages Required

4 page

Other font styles liked:
• I Welcome your creativity

Colors
59FF00
82FF00
B8FF75
E3FFCB
F4FFEA

Requirements
Must have
• Options to purchase : One product ($34.95); 2 products ($31.45 each - 10% discount), or 3 Products ($27.95 each - 20% discount)
Nice to have
• Focus on the Benefits of having all these Ingredients - Nutrients in one bottle - Essential Vitamins, Minerals, and proprietary blend of 42 Fruits and Vegetables.

```html
<!DOCTYPE html>
<html lang="en">
<head>
<meta charset="utf-8">
<title>Verdant Vigor – Vegan Nutritional Supplement</title>
<link rel="stylesheet" href="https://fonts.googleapis.com/css2?family=Cinzel:wght@400;600;700&family=Crimson+Text:wght@400;600&display=swap">
<style>
:root{
  --forest:#2d6a30;
  --forest-deep:#24572a;
  --lime:#82ff00;
  --lime-bright:#59ff00;
  --lime-soft:#b8ff75;
  --mint:#e3ffcb;
  --mist:#f4ffea;
  --white:#ffffff;
  --ink:#2b3a2b;
  --head-green:#2f6d2c;
}
*{margin:0;padding:0;box-sizing:border-box}
html,body{width:1200px;height:3999px;overflow:hidden;background:var(--white)}
body{position:relative;font-family:"Crimson Text",Georgia,serif;color:var(--ink)}
.abs{position:absolute}
.sc{font-family:"Cinzel",Georgia,serif}

/* header */
.site-header{left:0;top:0;width:1200px;height:92px;background:var(--forest);z-index:5}
.brand-box{left:98px;top:0;width:166px;height:118px;background:var(--forest);display:flex;align-items:flex-end;justify-content:center;padding-bottom:14px;z-index:6}
.brand-box span{font-family:"Cinzel",serif;font-weight:700;color:var(--white);font-size:24px;line-height:1.05;text-align:center}
.main-nav{top:60px;left:530px;display:flex;gap:0;z-index:6}
.main-nav a{font-family:"Cinzel",serif;font-weight:600;font-size:14px;color:var(--white);text-decoration:none;margin-right:46px}
.cart{left:878px;top:18px;color:var(--white);font-size:12px;display:flex;align-items:center;gap:8px;z-index:6;font-family:Arial,sans-serif}
.btn{display:inline-flex;align-items:center;justify-content:center;background:var(--lime);color:var(--forest-deep);font-family:"Cinzel",serif;font-weight:700;border-radius:20px;text-decoration:none}
.buy-now{left:1006px;top:10px;width:94px;height:34px;font-size:12px;z-index:6}

/* hero */
.hero-photo{left:0;top:92px;width:1200px;height:620px;background:linear-gradient(100deg,#eef0dc 0%,#dfe6c8 30%,#c9d3a6 55%,#b9b48e 75%,#d6d7c0 100%)}
.hero-title-sm{left:98px;top:186px;font-size:44px;color:var(--head-green);font-weight:600}
.hero-title{left:98px;top:236px;font-size:74px;color:var(--head-green);font-weight:600;letter-spacing:1px}
.hero-copy{left:98px;top:330px;width:500px;font-family:"Cinzel",serif;font-weight:700;font-size:13px;line-height:25px;color:#1c2a1c}
.hero-cta{left:98px;top:432px;width:122px;height:38px;font-size:14px}
.wave{left:0;top:540px}
.hero-bottle{left:0;top:512px;width:213px;height:463px;border-radius:24px 24px 30px 30px;background:linear-gradient(180deg,#f3f3f3 0 16%,#3d7a3b 16% 88%,#e9e9e9 88%)}
.badge{left:551px;top:635px;width:98px;height:98px}
.badge-text{left:551px;top:667px;width:98px;text-align:center;color:var(--white);font-family:Arial,sans-serif;font-size:22px}
.hero-sub{left:0;top:733px;width:1200px;text-align:center;font-size:20px;color:var(--forest-deep);font-weight:600}
.hero-h2{left:0;top:784px;width:1200px;text-align:center;font-size:29px;color:var(--forest-deep);font-weight:700}
.hero-para{left:280px;top:838px;width:640px;text-align:center;font-size:15px;line-height:23px;color:#2a3a22}

/* products */
.section-title{width:1200px;left:0;text-align:center;font-family:"Cinzel",serif;font-weight:700;color:var(--forest-deep)}
.products-title{top:1060px;font-size:38px}
.card{top:1192px;width:321px;height:337px;background:var(--lime-soft);border-radius:24px}
.card-inner{position:absolute;left:14px;top:14px;right:14px;height:265px;background:var(--white);border-radius:22px}
.card-price{position:absolute;left:0;right:0;bottom:14px;text-align:center;font-family:"Cinzel",serif;font-weight:600;font-size:17px;color:#1f3a1a}
.bottle{background:linear-gradient(180deg,#efefef 0 20%,#3d7a3b 20% 92%,#e8e8e8 92%);border-radius:20px 20px 24px 24px}
.card-label{top:1545px;width:321px;text-align:center;font-family:"Cinzel",serif;font-weight:600;font-size:25px;color:var(--forest-deep)}
.plus{top:1597px;width:62px;height:62px;border-radius:50%;background:radial-gradient(circle at 40% 35%,var(--lime) 0,var(--lime-bright) 70%);color:var(--forest-deep);font-size:30px;display:flex;align-items:center;justify-content:center;font-family:Arial,sans-serif}

/* ingredients */
.ingr-bg{left:0;top:1749px;width:1200px;height:672px;background:linear-gradient(180deg,#e9ece4 0%,#f2f3ee 45%,#dfe6d4 70%,#7fa54a 85%,#b9452e 100%)}
.ingr-title{top:1820px;font-size:34px}
.ingr-icon{width:80px;height:80px;border-radius:50%;background:var(--lime-bright)}
.ingr-icon.pale{background:var(--lime-soft)}
.ingr-item{width:240px}
.ingr-item h3{font-family:"Cinzel",serif;font-weight:600;font-size:16px;color:#3a3a2a;line-height:22px}
.ingr-item p{font-family:"Cinzel",serif;font-size:11.5px;line-height:16px;color:#7d8074;margin-top:4px}
.ingr-bottle{left:466px;top:1921px;width:268px;height:492px}

/* about */
.about-h{left:98px;font-family:"Cinzel",serif;font-weight:600;color:var(--head-green);font-size:40px}
.about-copy{left:98px;top:2683px;width:486px;font-size:16.5px;line-height:21.5px;color:#333}
.about-cta{left:98px;top:2900px;width:122px;height:40px;font-size:14px}
.about-photo{left:678px;top:2478px;width:490px;height:490px;border-radius:50%;background:radial-gradient(circle at 55% 45%,#ececec 0,#c9cfc2 45%,#5f8a4a 80%,#43703a 100%)}

/* benefits */
.benefits{left:0;top:3050px;width:1200px;height:554px;background:linear-gradient(135deg,var(--lime) 0%,#7ef500 50%,#8fff1c 100%)}
.benefits-title{top:3128px;font-size:32px;line-height:37px;color:var(--forest-deep);font-weight:600}
.benefit-circle{width:156px;height:156px;border-radius:50%;background:var(--white);border:8px solid var(--lime-soft)}
.benefit-circle.active{border-color:var(--forest-deep)}
.benefit-text{width:240px;text-align:center;font-family:"Cinzel",serif;font-size:14px;line-height:26px;color:#2d6a1d;font-weight:600}

/* footer */
.site-footer{left:0;top:3604px;width:1200px;height:395px;background:linear-gradient(180deg,#3b7e37 0%,var(--forest) 100%)}
.footer-brand{left:0;top:3700px;width:1200px;text-align:center;font-family:"Cinzel",serif;font-weight:700;color:var(--white);font-size:40px;line-height:44px}
.contact-line{display:flex;align-items:center;gap:10px;color:var(--white);font-family:"Cinzel",serif;font-size:16px}
.footer-nav{top:3853px;left:0;width:1200px;display:flex;justify-content:center;gap:52px}
.footer-nav a{font-family:"Cinzel",serif;font-weight:700;font-size:16px;color:var(--white);text-decoration:none}
.footer-rule{left:98px;top:3919px;width:1004px;height:1px;background:rgba(255,255,255,.6)}
.copyright{left:98px;top:3946px;font-family:"Cinzel",serif;font-size:13px;color:var(--white)}
.social{left:842px;top:3944px;display:flex;align-items:center;gap:14px;font-family:"Cinzel",serif;font-size:13px;color:var(--white)}
.social i{display:inline-block;width:14px;height:14px;border-radius:50%;background:var(--white)}
</style>
</head>
<body>

<header class="abs site-header"></header>
<div class="abs brand-box"><span>Verdant<br>Vigor</span></div>
<div class="abs cart">
  <svg width="18" height="16" viewBox="0 0 18 16"><path d="M0 1h3l2 9h10l2-7H5" fill="none" stroke="#fff" stroke-width="2"/><circle cx="7" cy="14" r="1.6" fill="#fff"/><circle cx="14" cy="14" r="1.6" fill="#fff"/></svg>
  Cart (0) Items
</div>
<a class="abs btn buy-now" href="#">Buy Now</a>
<nav class="abs main-nav">
  <a href="#">Home</a><a href="#">Products ⌄</a><a href="#">About Us</a><a href="#">Benefits ⌄</a><a href="#">Contact Us</a>
</nav>

<section>
  <div class="abs hero-photo" role="img" aria-label="Joyful woman with arms open in a sunny green park"></div>
  <h2 class="abs sc hero-title-sm">Welcome to</h2>
  <h1 class="abs sc hero-title">VERDANT VIGOR</h1>
  <p class="abs hero-copy">LOREM IPSUM DOLOR SIT AMET, CONSECTETUR ADIPISCING ELIT, SED DO EIUSMOD TEMPOR INCIDIDUNT UT LABORE ET DOLORE MAGNA ALIQUA.</p>
  <a class="abs btn hero-cta" href="#">Contact Us</a>

  <svg class="abs wave" width="1200" height="460" viewBox="0 540 1200 460">
    <path d="M0 640 L233 620 C380 590 480 571 598 571 C760 571 900 667 1087 667 C1140 667 1180 620 1200 590 L1200 890 C1000 930 800 975 600 975 C400 975 200 940 0 910 Z" fill="#b8ff75"/>
    <path d="M140 930 C350 960 450 982 600 982 C800 982 1000 940 1200 895" fill="none" stroke="#2d6a30" stroke-width="4"/>
  </svg>
  <div class="abs hero-bottle" role="img" aria-label="Supplement bottle with green label"></div>
  <svg class="abs badge" viewBox="0 0 100 100"><path d="M50 2 L60 9 L72 6 L77 17 L89 20 L88 32 L97 40 L91 51 L97 62 L88 69 L89 81 L77 83 L72 94 L60 91 L50 98 L40 91 L28 94 L23 83 L11 81 L12 69 L3 62 L9 51 L3 40 L12 32 L11 20 L23 17 L28 6 L40 9 Z" fill="#24572a"/></svg>
  <div class="abs badge-text">100%</div>
  <div class="abs sc hero-sub">Verdant Vigor</div>
  <h2 class="abs sc hero-h2">Immune Health, Heart Health, and Brain Health.</h2>
  <p class="abs hero-para">Lorem ipsum dolor sit amet, consectetur adipiscing elit, sed do eiusmod tempor incididunt ut labore et dolore magna aliqua. Ut enim ad minim veniam,</p>
</section>

<section>
  <h2 class="abs section-title products-title">OUR PRODUCT</h2>

  <div class="abs card" style="left:93px"><div class="card-inner"></div><div class="card-price">$34.95</div></div>
  <div class="abs card" style="left:435px"><div class="card-inner"></div><div class="card-price">$31.45 each - 10% discount</div></div>
  <div class="abs card" style="left:776px"><div class="card-inner"></div><div class="card-price">$27.95 each - 20% discount</div></div>

  <div class="abs bottle" style="left:168px;top:1138px;width:172px;height:306px" role="img" aria-label="Supplement bottle"></div>
  <div class="abs bottle" style="left:513px;top:1138px;width:172px;height:306px" role="img" aria-label="Supplement bottle"></div>
  <div class="abs bottle" style="left:861px;top:1138px;width:172px;height:306px" role="img" aria-label="Supplement bottle"></div>

  <div class="abs card-label" style="left:93px">ONE PRODUCT</div>
  <div class="abs card-label" style="left:435px">TWO PRODUCT</div>
  <div class="abs card-label" style="left:776px">THREE PRODUCT</div>

  <div class="abs plus" style="left:223px">+</div>
  <div class="abs plus" style="left:565px">+</div>
  <div class="abs plus" style="left:906px">+</div>
</section>

<section>
  <div class="abs ingr-bg" role="img" aria-label="Whitewashed wooden boards with fresh vegetables and fruit along the bottom"></div>
  <svg class="abs" style="left:0;top:2330px" width="1200" height="95" viewBox="0 0 1200 95"><path d="M0 95 L0 70 C300 20 500 0 600 0 C700 0 900 20 1200 60 L1200 95 Z" fill="none"/><path d="M0 95 L1200 95 L1200 91 L0 91 Z" fill="#fff"/></svg>
  <h2 class="abs section-title ingr-title">INGREDIENTS AND THEIR BENEFITS</h2>

  <div class="abs ingr-icon" style="left:106px;top:1978px" role="img" aria-label="Vitamin icon"></div>
  <div class="abs ingr-item" style="left:203px;top:1975px"><h3>It Contains Essential Vitamins</h3><p>SED UT PERSPICIATIS UNDE OMNIS ISTE NATUS ERROR SIT VOLUPTATEM</p></div>

  <div class="abs ingr-icon pale" style="left:106px;top:2114px" role="img" aria-label="Minerals icon"></div>
  <div class="abs ingr-item" style="left:203px;top:2113px"><h3>Minerals</h3><p>SED UT PERSPICIATIS UNDE OMNIS ISTE NATUS ERROR SIT VOLUPTATEM</p></div>

  <div class="abs ingr-icon pale" style="left:764px;top:1978px" role="img" aria-label="Fruit basket icon"></div>
  <div class="abs ingr-item" style="left:863px;top:1975px"><h3>Proprietary Blend of 42 Fruits and Vegetables.</h3><p>SED UT PERSPICIATIS UNDE OMNIS ISTE NATUS ERROR SIT VOLUPTATEM</p></div>

  <div class="abs ingr-icon pale" style="left:764px;top:2114px" role="img" aria-label="Nutrients icon"></div>
  <div class="abs ingr-item" style="left:863px;top:2115px"><h3>Nutrients in One Bottle</h3><p>SED UT PERSPICIATIS UNDE OMNIS ISTE NATUS ERROR SIT VOLUPTATEM</p></div>

  <div class="abs bottle ingr-bottle" role="img" aria-label="Supplement bottle with green label"></div>
</section>

<section>
  <h2 class="abs about-h" style="top:2545px">ABOUT US</h2>
  <h2 class="abs about-h" style="top:2608px">VERDANT VIGOR</h2>
  <p class="abs about-copy">Sed ut perspiciatis unde omnis iste natus error sit voluptatem accusantium doloremque laudantium, totam rem aperiam, eaque ipsa quae ab illo inventore veritatis et quasi architecto beatae vitae dicta sunt explicabo. Nemo enim ipsam voluptatem quia voluptas sit aspernatur aut odit aut fugit, sed quia consequuntur magni dolores eos qui ratione voluptatem sequi nesciunt. Neque porro quisquam est, qui dolorem ipsum quia dolor sit amet, consectetur, adipisci velit, sed quia non numquam eius modi tempora incidunt ut labore et dolore magnam aliquam quaerat voluptatem.</p>
  <a class="abs btn about-cta" href="#">Contact Us</a>
  <div class="abs about-photo" role="img" aria-label="Smiling woman in a white tee raising her fist, in front of greenery"></div>
</section>

<section>
  <div class="abs benefits"></div>
  <h2 class="abs section-title benefits-title">Verdant Vigor - A Powerful Supplement<br>for Getting Optimal Health</h2>

  <div class="abs benefit-circle" style="left:124px;top:3259px" role="img" aria-label="Capsule icon"></div>
  <div class="abs benefit-circle active" style="left:388px;top:3259px" role="img" aria-label="Blood cells icon"></div>
  <div class="abs benefit-circle" style="left:653px;top:3259px" role="img" aria-label="Heart icon"></div>
  <div class="abs benefit-circle" style="left:918px;top:3259px" role="img" aria-label="Hands holding brain icon"></div>

  <p class="abs benefit-text" style="left:82px;top:3432px">It May Help Increase Energy (ATP) and Regulate Metabolism</p>
  <p class="abs benefit-text" style="left:346px;top:3432px">It May Help the Formation of Red Blood Cells</p>
  <p class="abs benefit-text" style="left:601px;top:3432px;width:260px">It May Help Strengthen the Immune System and Reduce Cancer and Heart Disease Risk</p>
  <p class="abs benefit-text" style="left:876px;top:3432px">It May Help Improve Mental Health</p>
</section>

<footer>
  <div class="abs site-footer"></div>
  <div class="abs footer-brand">VERDANT<br>VIGOR</div>
  <div class="abs contact-line" style="left:100px;top:3760px">
    <svg width="20" height="15" viewBox="0 0 20 15"><rect x="1" y="1" width="18" height="13" fill="none" stroke="#fff" stroke-width="1.6"/><path d="M1 1 L10 8 L19 1" fill="none" stroke="#fff" stroke-width="1.6"/></svg>
    INFO@VERDANTVIGOR.COM
  </div>
  <div class="abs contact-line" style="left:861px;top:3752px;font-family:'Crimson Text',serif;font-size:21px">
    <svg width="16" height="16" viewBox="0 0 24 24"><path d="M6.6 10.8a15 15 0 0 0 6.6 6.6l2.2-2.2c.3-.3.7-.4 1-.2 1.1.4 2.3.6 3.6.6.6 0 1 .4 1 1V20c0 .6-.4 1-1 1A17 17 0 0 1 3 4c0-.6.4-1 1-1h3.5c.6 0 1 .4 1 1 0 1.3.2 2.5.6 3.6.1.3 0 .7-.2 1z" fill="#fff"/></svg>
    +1 555-010-0199
  </div>
  <nav class="abs footer-nav">
    <a href="#">Home</a><a href="#">Products ⌄</a><a href="#">About Us</a><a href="#">Benefits ⌄</a><a href="#">Contact Us</a>
  </nav>
  <div class="abs footer-rule"></div>
  <p class="abs copyright">© Copyrights 2022 &nbsp;Verdant Vigor | &nbsp;All Rights Reserved</p>
  <div class="abs social">Social Media : <i></i><i></i><i></i><i></i></div>
</footer>

</body>
</html>
```